Simple Logo Design for Semi-Clear Plastic Frosted Card stock

Create a business card on frosted plastic. compliment existing logo elements with a tree trunk, roots, or seed at the lower half and the full logo both on the front.

Contact information will go on a solid portion of the back of this design since this card stock is semi-transparent.

It is important to consider this plastic card stock medium in your design. I found helpful tips and guides listed at vellaprint-sample.net: be careful to understand ink printed on plastic cards cannot have too much of a consistent print area or risks peeling and fine lines can easily scratch off.
Updates

2" x 3.5" 20PT Clear Plastic Business cards with Round corners Please get info or templates here: https://www.vellaprint-sample.net/product-detail/2-x-35-20pt-clear-plastic-business-cards-with-round-corners

Target Market(s)

Not for profit- religion

Industry/Entity Type

Business

Must include complementary elements to the existing logo

Font styles to use
Decorative

Colors
000000

Requirements
Must have
• Elements of community, nature and oneness. Such as: seed, roots, tree trunk, etc.
• Three lines of space on the back for Name, Title, Phone Number.
Nice to have
• I like a light use of decorative elements
Should not have
• No eyes, from faces or animals.

```html
<!DOCTYPE html>
<html lang="en">
<head>
<meta charset="utf-8">
<title>Meadowroot Circle – Frosted Business Card</title>
<link rel="stylesheet" href="https://fonts.googleapis.com/css2?family=Didact+Gothic&family=Open+Sans:wght@600&display=swap">
<style>
  :root {
    --canvas: #d9d4cc;
    --frost-top: #f1f4f5;
    --frost-bottom: #e4e9ea;
    --card-edge: rgba(255,255,255,0.8);
    --brand-green: #0f4a3c;
    --leaf-dark: #1f5e22;
    --leaf-light: #4c8c34;
    --band-dark: #0c3f33;
    --band-light: #1c5e4b;
    --rule: #a6b58a;
    --name-ink: #cfc7b8;
    --title-ink: #a3453d;
    --tagline-ink: #1e2a25;
    --ghost-green: rgba(15,74,60,0.42);
  }
  * { margin: 0; padding: 0; box-sizing: border-box; }
  html, body { width: 1200px; height: 685px; overflow: hidden; }
  body {
    background: var(--canvas);
    font-family: "Didact Gothic", "Century Gothic", sans-serif;
    position: relative;
  }
  .card {
    position: absolute;
    top: 224px;
    width: 455px;
    height: 259px;
    border-radius: 14px;
    overflow: hidden;
    background: linear-gradient(180deg, var(--frost-top), var(--frost-bottom));
    border: 1px solid var(--card-edge);
    box-shadow: 0 6px 18px rgba(0,0,0,0.12);
  }
  .card--front { left: 123px; }
  .card--back  { left: 602px; }

  .brand {
    position: absolute;
    left: 0; right: 0;
    top: 21px;
    text-align: center;
  }
  .brand__dot {
    display: block;
    width: 64px; height: 64px;
    margin: 0 auto 14px;
    border-radius: 50%;
    background: var(--brand-green);
  }
  .brand__name {
    display: block;
    font-size: 24px;
    letter-spacing: 0.5px;
    color: var(--brand-green);
    text-transform: uppercase;
    line-height: 1;
  }
  .brand__tagline {
    display: block;
    margin-top: 4px;
    font-size: 9px;
    letter-spacing: 0.4px;
    color: var(--tagline-ink);
    text-transform: uppercase;
  }
  .brand--ghost { transform: scaleX(-1); }
  .brand--ghost .brand__dot { background: var(--ghost-green); }
  .brand--ghost .brand__name,
  .brand--ghost .brand__tagline { color: var(--ghost-green); }

  .foliage {
    position: absolute;
    left: 0; right: 0;
    top: 153px;
    height: 37px;
    background: linear-gradient(180deg, rgba(76,140,52,0) 0%, rgba(76,140,52,0.55) 35%, var(--leaf-dark) 100%);
  }
  .band {
    position: absolute;
    left: 0; right: 0; bottom: 0;
    height: 68px;
    background: linear-gradient(180deg, var(--band-light), var(--band-dark));
    border-top: 2px solid var(--rule);
    display: flex;
    align-items: center;
    justify-content: center;
  }
  .person {
    font-family: "Open Sans", sans-serif;
    font-weight: 600;
    font-size: 23px;
    color: var(--name-ink);
    letter-spacing: 0.3px;
  }
  .person__title {
    font-family: "Didact Gothic", sans-serif;
    font-weight: 400;
    color: var(--title-ink);
    font-size: 19px;
  }
  .phone {
    font-family: "Didact Gothic", sans-serif;
    font-size: 37px;
    color: var(--name-ink);
    letter-spacing: 1px;
  }
</style>
</head>
<body>
  <section class="card card--front">
    <div class="brand">
      <span class="brand__dot"></span>
      <span class="brand__name">Meadowroot Circle</span>
      <span class="brand__tagline">Learning, Fellowship &amp; Calm</span>
    </div>
    <div class="foliage" role="img" aria-label="Row of green leafy vines along the card"></div>
    <div class="band">
      <p class="person">Daniel Hart <span class="person__title">- CEO/Founder</span></p>
    </div>
  </section>

  <section class="card card--back">
    <div class="brand brand--ghost" aria-hidden="true">
      <span class="brand__dot"></span>
      <span class="brand__name">Meadowroot Circle</span>
      <span class="brand__tagline">Learning, Fellowship &amp; Calm</span>
    </div>
    <div class="foliage" role="img" aria-label="Row of green leafy vines along the card"></div>
    <div class="band">
      <p class="phone">555 014 2290</p>
    </div>
  </section>
</body>
</html>
```